Overwhelmed with Oil and Gas letters?

My company (PlotVaultLand) has developed a solution for landowners trying to get the best price and deal with a legitimate buyer who will pay money for their minerals (oil & gas rights)... I need to have a post card designed that reflects landowners are getting overwhelmed with constant letters, offers, etc... I have a attached a couple files that I was working on but need to have something creative designed for the front of the card.

Target Market(s)

landowner consumers in rural area

Industry/Entity Type

It Company

Requirements
Must have
• overwhelmed or drowning with many offer letters or mail. PlotVaultLand is a One Stop Market that PreScreens buyers and has them compete to drive the offer price higher.

```html
<!DOCTYPE html>
<html lang="en">
<head>
<meta charset="utf-8">
<title>PlotVaultLand Postcard</title>
<link href="https://fonts.googleapis.com/css2?family=Arimo:wght@400;700&family=Archivo+Black&family=Montserrat:wght@400;600&family=Noto+Serif:wght@400;700&display=swap" rel="stylesheet">
<style>
:root{
  --backdrop:#1f1f1f;
  --navy:#1c3564;
  --navy-dark:#152a52;
  --green:#8bc03f;
  --green-dark:#6fa52a;
  --white:#ffffff;
  --line-grey:#9a9a9a;
  --text-grey:#7a7a7a;
}
*{margin:0;padding:0;box-sizing:border-box}
html,body{width:1028px;height:1200px;overflow:hidden;background:var(--backdrop)}
.card{position:absolute;background:var(--white);overflow:hidden}
.card-front{left:176px;top:39px;width:685px;height:531px;background:radial-gradient(ellipse at 60% 40%,#fff 40%,#e9e9e9 100%)}
.card-back{left:177px;top:614px;width:687px;height:534px}
.abs{position:absolute}
.brand-name{font-family:"Arimo",sans-serif;font-weight:700;color:var(--navy);white-space:nowrap;letter-spacing:-0.5px}
.front-brand{left:38px;top:64px;font-size:27px}
.headline-banner{left:242px;top:34px;width:404px;height:80px;background:linear-gradient(#24457e,var(--navy-dark));box-shadow:0 4px 6px rgba(0,0,0,.35);text-align:center;padding-top:6px}
.banner-line1{font-family:"Arimo",sans-serif;font-weight:700;color:var(--white);font-size:29px;line-height:30px}
.banner-line2{font-family:"Archivo Black",sans-serif;color:var(--green);font-size:38px;line-height:40px;letter-spacing:1px}
.headline{left:40px;top:205px;font-family:"Arimo",sans-serif;font-weight:700;line-height:1}
.headline .navy{color:var(--navy);font-size:36px;display:block;margin-bottom:7px}
.headline .promise{color:var(--green);font-family:"Archivo Black",sans-serif;font-size:44px;display:block;margin-bottom:5px}
.headline .green{color:var(--green);font-size:36px;display:block}
.scene-area{left:330px;top:130px;width:340px;height:320px;background:radial-gradient(ellipse at 45% 55%,#cfd6de 0%,#e8ecef 50%,rgba(240,240,240,0) 70%)}
.call-title{left:0;width:685px;top:436px;text-align:center;font-family:"Archivo Black",sans-serif;color:var(--navy);font-size:31px;letter-spacing:1px}
.contact-row{left:0;width:685px;top:470px;display:flex;justify-content:center;align-items:center;color:var(--white);font-family:"Arimo",sans-serif;font-weight:700}
.contact-row .phone{font-size:30px;padding-right:10px}
.contact-row .divider{width:2px;height:34px;background:var(--white)}
.contact-row .web{font-size:22px;padding-left:11px}
.back-panel{left:0;top:0;width:542px;height:171px;background:linear-gradient(90deg,#fff 60%,#e3e3e3 100%)}
.back-panel-lower{left:0;top:385px;width:332px;height:56px;background:linear-gradient(90deg,#e6e6e6,#fff 40%,#fff 60%,#e6e6e6)}
.solution-banner{left:29px;top:31px;width:283px;height:57px;background:linear-gradient(#24457e,var(--navy-dark));box-shadow:0 4px 6px rgba(0,0,0,.35);font-family:"Noto Serif",serif;color:var(--white);text-align:center;line-height:1}
.solution-banner .l1{font-size:20px;display:block;padding-top:5px}
.solution-banner .l2{font-size:16px}
.solution-banner .works{font-size:33px;font-weight:700;color:var(--green);letter-spacing:.5px}
.story{left:44px;top:104px;width:262px;font-family:"Montserrat",sans-serif;font-size:11.4px;line-height:15.2px;letter-spacing:-0.2px;color:var(--navy)}
.story p{margin-bottom:15px;text-align:justify;hyphens:auto}
.story strong{font-weight:600}
.story .accent{color:var(--green-dark)}
.cta-strip{left:0;top:349px;width:332px;height:36px;background:var(--green);text-align:center;font-family:"Arimo",sans-serif;font-weight:700;font-size:13.4px;line-height:15.5px;color:var(--navy);padding-top:3px}
.cta-strip .hl{color:var(--white)}
.back-phone{left:0;width:332px;top:390px;text-align:center;font-family:"Arimo",sans-serif;font-weight:700;font-size:24px;color:var(--navy)}
.back-web{left:0;width:332px;top:416px;text-align:center;font-family:"Arimo",sans-serif;font-size:20px;color:var(--green-dark)}
.back-brand{left:316px;width:210px;top:56px;text-align:center;font-size:25px}
.address{left:316px;width:210px;top:104px;text-align:center;font-family:"Noto Serif",serif;font-size:17px;line-height:21px;color:var(--navy)}
.stamp-box{left:547px;top:39px;width:90px;height:103px;border:1px solid #b5b5b5;font-family:"Arimo",sans-serif;font-size:16px;line-height:20px;color:var(--text-grey);padding:25px 0 0 23px}
.address-line{left:360px;width:283px;height:1px;background:var(--line-grey)}
</style>
</head>
<body>

<section class="card card-front">
  <svg class="abs" style="left:0;top:0" width="685" height="531" viewBox="0 0 685 531">
    <path d="M30 190 C 180 160, 370 160, 395 210 C 405 240, 360 270, 310 290 C 380 255, 385 215, 320 200 C 240 185, 120 182, 30 190 Z" fill="var(--green)"/>
    <path d="M0 438 C 120 460, 300 445, 420 400 C 520 370, 620 368, 685 380 L685 531 L0 531 Z" fill="var(--green)"/>
    <path d="M0 392 C 120 415, 300 405, 420 382 C 520 363, 620 368, 685 380 L685 393 C 620 380, 520 378, 420 398 C 300 420, 120 428, 0 405 Z" fill="var(--navy)"/>
  </svg>
  <div class="abs brand-name front-brand">PlotVaultLand</div>
  <div class="abs headline-banner">
    <div class="banner-line1">NATION’S ONLY OIL &amp; GAS</div>
    <div class="banner-line2">BIDDING SYSTEM</div>
  </div>
  <div class="abs scene-area" role="img" aria-label="Illustration of a landowner buried under a pile of offer letters, with a farmhouse and windmill behind him"></div>
  <h1 class="abs headline">
    <span class="navy">Tired Of All The</span>
    <span class="promise">Promi$e$</span>
    <span class="navy">From Oil &amp; Gas</span>
    <span class="green">Brokers?</span>
  </h1>
  <div class="abs call-title">CALL US TODAY</div>
  <div class="abs contact-row">
    <span class="phone">(877) 555-0142</span>
    <span class="divider"></span>
    <span class="web">www.plotvaultland.com</span>
  </div>
</section>

<section class="card card-back">
  <div class="abs back-panel"></div>
  <div class="abs back-panel-lower"></div>

  <div class="abs solution-banner">
    <span class="l1">Finally A Real Solution</span>
    <span class="l2">That </span><span class="works">WORKS</span>
  </div>

  <div class="abs story">
    <p><strong>PLOTVAULTLAND</strong> was started by a local land owner group that simply got fed up with getting the run around from mineral brokers stating that they could get them <span class="accent">“ TOP DOLLAR ”</span> for their oil &amp; gas rights.</p>
    <p><strong>PLOTVAULTLAND</strong> has developed a competitive bidding system that will connect you with our pre-screened buyer network. The bidding system allows our buyer network to place direct bids on your oil &amp; gas rights. In a competitive bidding environment the highest price wins ultimately giving you - the owner - the maximum price available.</p>
  </div>

  <div class="abs cta-strip">Please <span class="hl">Contact Us Today</span> and find out<br>how this proven system can work for you</div>
  <div class="abs back-phone">(877) 555-0142</div>
  <div class="abs back-web">www.plotvaultland.com</div>

  <div class="abs brand-name back-brand">PlotVaultLand</div>
  <div class="abs address">418 Cedar Hollow Rd<br>Millbrook, PA 15300</div>

  <div class="abs stamp-box">Place<br>Stamp<br>Here</div>

  <div class="abs address-line" style="top:254px"></div>
  <div class="abs address-line" style="top:310px"></div>
  <div class="abs address-line" style="top:369px"></div>
</section>

</body>
</html>
```